Design my dad a new business card because his current one sucks!

I need a business card designed for my fathers home maintenance business. His customers are individuals (single moms, old people etc.) as well as the occasional business. As such it needs to be accessible to both target audiences.

The front of the card should be dark grey on yellow with the logo and contain the following information:
- Darren Holtwick
- 0488 274 915
- info@brightoakhomecare.com.au
- 0488 274 915

- ABN: 71 284 630 912
- 'Fully Insured'

The reverse should be yellow on dark grey and will have the web address:
- brightoakhomecare.com.au

And a few key services he offers:
GENERAL REPAIRS
PAINTING/TILING/
PAVING &CONCRETING
PRESSURE WASHING
ON-SITE WELDING
DECKING ADDITIONS & REPAIRS
FENCING
FULL BOND CLEANING

This will be first time the logo has been printed so you will need to come up with the best CMYK approximation of the RGB colours to make sure it is a close as possible.

```html
<!DOCTYPE html>
<html lang="en">
<head>
<meta charset="utf-8">
<title>Brightoak Home Care – Business Card</title>
<link href="https://fonts.googleapis.com/css2?family=Roboto+Condensed:wght@400;700&family=Ubuntu:wght@400;700&display=swap" rel="stylesheet">
<style>
  :root {
    --stage: #e0e0de;
    --charcoal: #4a4645;
    --yellow-core: #fff200;
    --yellow-edge: #f6c100;
    --yellow-text: #ffd500;
  }
  * { margin: 0; padding: 0; box-sizing: border-box; }
  html, body { width: 1090px; height: 1200px; overflow: hidden; background: var(--stage); }
  .canvas { position: relative; width: 1090px; height: 1200px; }

  .card { position: absolute; left: 67px; width: 955px; height: 543px; overflow: hidden; }

  /* Front */
  .card--front { top: 31px; background: radial-gradient(ellipse 60% 75% at 45% 40%, var(--yellow-core) 0%, #ffe500 40%, var(--yellow-edge) 100%); }
  .card__wave { position: absolute; inset: 0; width: 955px; height: 543px; }
  .phone { position: absolute; left: 61px; top: 62px; font: 400 39px/1 "Roboto Condensed", sans-serif; color: var(--charcoal); }
  .phone b { font-weight: 700; }
  .wordmark { position: absolute; font-family: "Ubuntu", sans-serif; font-weight: 700; line-height: 1; text-align: right; }
  .wordmark__name { display: block; font-size: 76px; letter-spacing: -1px; }
  .wordmark__tag { display: block; font-size: 21px; letter-spacing: 2px; margin-top: 6px; }
  .card--front .wordmark { right: 92px; top: 62px; color: var(--charcoal); }
  .details { position: absolute; left: 61px; top: 324px; font: 400 21px/36px "Roboto Condensed", sans-serif; color: var(--charcoal); }
  .details b { font-weight: 700; }
  .insured { position: absolute; right: 61px; top: 416px; font: 400 32px/1 "Ubuntu", sans-serif; color: var(--yellow-text); }

  /* Back */
  .card--back { top: 625px; background: var(--charcoal); }
  .card--back .wordmark { left: 0; right: 0; top: 58px; text-align: center; color: var(--yellow-text); }
  .services { position: absolute; left: 0; right: 0; top: 234px; text-align: center; list-style: none;
    font: 400 27px/42px "Roboto Condensed", sans-serif; color: var(--yellow-text); }
  .services li { white-space: nowrap; }
  .web-band { position: absolute; left: 0; right: 0; top: 415px; height: 68px;
    background: linear-gradient(90deg, var(--yellow-edge), var(--yellow-core) 50%, var(--yellow-edge));
    display: flex; align-items: center; justify-content: center;
    font: 400 29px/1 "Ubuntu", sans-serif; color: var(--charcoal); }
</style>
</head>
<body>
<div class="canvas">

  <section class="card card--front">
    <svg class="card__wave" viewBox="0 0 955 543" aria-hidden="true">
      <path d="M0,410 C180,500 380,500 560,420 C720,350 830,255 955,238 L955,543 L0,543 Z" fill="var(--charcoal)"/>
      <path d="M0,468 C140,500 260,520 420,505 C540,490 600,450 660,420 C580,470 480,520 330,543 L230,543 C170,520 90,495 0,480 Z" fill="var(--yellow-edge)"/>
      <path d="M120,445 C300,500 480,460 620,380 C740,310 850,265 955,250" stroke="var(--yellow-edge)" stroke-width="5" fill="none"/>
    </svg>
    <p class="phone"><b>Ph:</b> 0488 274 915</p>
    <div class="wordmark">
      <span class="wordmark__name">Brightoak</span>
      <span class="wordmark__tag">HOME CARE</span>
    </div>
    <p class="details">
      <b>Email:</b> info@brightoakhomecare.com.au<br>
      <b>ABN:</b> 71 284 630 912
    </p>
    <p class="insured">Fully Insured</p>
  </section>

  <section class="card card--back">
    <div class="wordmark">
      <span class="wordmark__name">Brightoak</span>
      <span class="wordmark__tag">HOME CARE</span>
    </div>
    <ul class="services">
      <li>GENERAL REPAIRS &nbsp;•&nbsp; PAINTING/TILING/ &nbsp;•&nbsp; PAVING &amp; CONCRETING</li>
      <li>PRESSURE WASHING • &nbsp;ON-SITE WELDING &nbsp;•&nbsp; DECKING ADDITIONS &amp; REPAIRS</li>
      <li>FENCING &nbsp;•&nbsp; FULL BOND CLEANING</li>
    </ul>
    <div class="web-band">www.brightoakhomecare.com.au</div>
  </section>

</div>
</body>
</html>
```